Packaging design for a reclosable bag for our product

We have a logo, and we need to put it on packaging for our product and while we want the look to be simple, we want it to follow good design principles and also contain spaces for other product descriptions.

There will be 5 sizes at launch so I'd like 5 variations, one for each size.

I've included a few mockups of the type of bag that I made but they are all just rough ideas that I had.

I want the brand to look scientific and methodical and even a bit quirky, as in "wow this is a serious product but also a bit unusual."

```html
<!DOCTYPE html>
<html lang="en">
<head>
<meta charset="utf-8">
<title>Bias Lighting Extra Largue – Pouch Front</title>
<link href="https://fonts.googleapis.com/css2?family=Barlow:wght@500;600;700&family=Barlow+Semi+Condensed:wght@600;700&display=swap" rel="stylesheet">
<style>
  :root {
    --backdrop: #2e2f33;
    --pouch: #f7f7f7;
    --ink: #141416;
    --paper: #ffffff;
  }
  * { margin: 0; padding: 0; box-sizing: border-box; }
  html, body {
    width: 1200px;
    height: 833px;
    overflow: hidden;
    background: var(--backdrop);
  }
  .canvas {
    position: relative;
    width: 1200px;
    height: 833px;
  }
  .pouch {
    position: absolute;
    left: 350px;
    top: 110px;
    width: 493px;
    height: 723px;
    background: var(--pouch);
    border-radius: 4px 4px 0 0;
    overflow: hidden;
  }
  .pouch-graphics {
    position: absolute;
    inset: 0;
  }
  .title-block {
    position: absolute;
    left: 0;
    right: 0;
    top: 134px;
    text-align: center;
    color: var(--ink);
    font-family: "Barlow", sans-serif;
  }
  .product-title {
    font-weight: 600;
    font-size: 27px;
    letter-spacing: 0.16em;
    margin-left: 0.16em;
  }
  .product-size {
    margin-top: 2px;
    font-weight: 500;
    font-size: 12px;
    letter-spacing: 0.42em;
    margin-left: 0.42em;
  }
  .brand-name {
    position: absolute;
    left: 78px;
    top: 286px;
    width: 344px;
    height: 196px;
    display: flex;
    align-items: center;
    justify-content: center;
    color: var(--paper);
    font-family: "Barlow", sans-serif;
    font-weight: 700;
    font-size: 76px;
    letter-spacing: 0.02em;
  }
  .length-badge {
    position: absolute;
    left: 96px;
    top: 572px;
    width: 50px;
    text-align: center;
    color: var(--ink);
    font-family: "Barlow Semi Condensed", sans-serif;
  }
  .length-value {
    font-weight: 700;
    font-size: 27px;
    line-height: 1;
  }
  .length-unit {
    font-weight: 600;
    font-size: 9px;
    letter-spacing: 0.04em;
    margin-top: 3px;
  }
  .spec-lines {
    position: absolute;
    left: 230px;
    top: 578px;
    width: 210px;
    text-align: center;
    color: var(--ink);
    font-family: "Barlow Semi Condensed", sans-serif;
    font-weight: 700;
    font-size: 14px;
    line-height: 1.2;
  }
</style>
</head>
<body>
  <main class="canvas">
    <section class="pouch">
      <svg class="pouch-graphics" width="493" height="723" viewBox="0 0 493 723" aria-hidden="true">
        <polygon class="diagonal-top" points="493,58 493,78 353,268 333,268" fill="var(--ink)"/>
        <rect class="band-line-top" x="26" y="261" width="412" height="14" fill="var(--ink)"/>
        <rect class="brand-block" x="78" y="286" width="344" height="196" fill="var(--ink)"/>
        <rect class="band-line-bottom" x="26" y="537" width="412" height="11" fill="var(--ink)"/>
        <polygon class="diagonal-bottom" points="224,555 242,555 127,723 109,723" fill="var(--ink)"/>
      </svg>

      <header class="title-block">
        <h1 class="product-title">BIAS LIGHTING</h1>
        <p class="product-size">EXTRA LARGUE</p>
      </header>

      <div class="brand-name">KELVRA</div>

      <div class="length-badge">
        <div class="length-value">5</div>
        <div class="length-unit">METERS</div>
      </div>

      <p class="spec-lines">SIMULATED D65 CRI 90+<br>6500K WHITE BIAS LIGHTING</p>
    </section>
  </main>
</body>
</html>
```